Mens Jewellery Homepage - Modern, Stylish Mens Ring Brand - Homepage

Project Overview: KestrelHoops.com is a men's accessories brand specializing in high-quality mens rings.

The objective of this redesign is to create a modern, visually appealing homepage that is easy to navigate, showcases a wide range of rings, highlights personalization options, and builds trust with customers.

The new design should make a strong impression while reflecting the brand's premium quality and commitment to craftsmanship.

The focus will be on a sleek aesthetic that aligns with the tastes of men shopping for wedding bands, engagement rings, or fashion accessories.

Objectives:

Modern and Sleek Aesthetic:

A clean, minimalist design that emphasizes high-quality product imagery and thoughtful use of space.
Contemporary color palette that conveys elegance and sophistication, with accents that highlight key elements without overwhelming the user.

Consistent and easy-to-read typography that reflects the brand’s modern and masculine identity.

Showcasing Products:
Hero Section: A image to show off 3 or 4 ring designs that could be used for weddings or fashion.

Product Highlights: Below the hero banner, showcase product categories by color (see current website for colors)

Featured Products: Display a selection of “Top Rated” or “Customer Favorites” rings to help guide users toward popular choices.

Personalization Section:
A dedicated section promoting the ability to personalize rings, emphasizing features like engraving with names, dates, or special messages.
Include lifestyle images of personalized rings to inspire customers and give them an idea of what’s possible.
Use callouts such as “Make It Yours” or “Personalize Your Ring” to encourage users to explore the customization options available for each product.

Building Trust:

A space to show 5 or 6 testimonials and other trust elements

Symbols / text to show

free delivery
free returns
every ring stock
fast delivery
customer images (from reviews)

Driving Conversions:
Include a prominent call-to-action (CTA) button in the hero section with text like “Shop Now” or “Discover Our Collections.”

User Experience:
Fast, easy-to-navigate layout with simple and intuitive categories. Product categories and main sections should be clearly visible and easy to access without overwhelming the user.
Design the homepage to feel cohesive and uncluttered, with a logical flow from product discovery to personalization and checkout.

Visual Elements and Imagery:
Use ring images from our site, but add backgrounds etc to make the image on the homepage more interesting.

Personalization Options: Use visual representations (like ring mockups) showing where personalization options (such as engravings) would appear on the product.

I like (and would like to see some different designs from our current design)
Vorm.com for design
ridgeloops.com

Target Market(s)

Men - 20 to 35

Number of Pages Required

1 page

Requirements
Must have
• Easy navigation, Trust, Modern, Clean,
Nice to have
• Would like to see Different designs like Vorm.com - RidgeLoops.com

```html
<!DOCTYPE html>
<html lang="en">
<head>
<meta charset="utf-8">
<title>Kestrel Hoops – Men's Rings</title>
<link href="https://fonts.googleapis.com/css2?family=Archivo:wght@400;500;600;700&family=Lato:wght@400;700&display=swap" rel="stylesheet">
<style>
:root{
  --hero-bg:#e6d6c0;
  --brown:#8a4714;
  --ink:#222;
  --muted:#555;
  --card:#ede3d5;
  --price:#137a72;
  --dark:#2a2117;
  --dark-line:#4a3d2f;
  --gold:#d6a94a;
  --bar:#f3e5b6;
  --white:#fff;
}
*{box-sizing:border-box;margin:0;padding:0}
html,body{width:1200px;height:3089px;overflow:hidden;background:var(--white)}
body{font-family:"Archivo",sans-serif;color:var(--ink);position:relative}
.abs{position:absolute}
.brand{display:flex;align-items:center;gap:10px;font-family:"Archivo",sans-serif;font-weight:600;text-transform:uppercase}
.brand .dot{border-radius:50%;border:3px solid currentColor;flex:none}
.brand .word{display:flex;flex-direction:column;letter-spacing:5px}
/* header / hero */
.hero{left:0;top:0;width:1200px;height:534px;background:linear-gradient(100deg,#e9dac6 0%,#e4d2bb 55%,#dcc8ad 100%)}
.hero .brand{left:174px;top:22px;color:#2a2a2a;font-size:16px;line-height:18px}
.hero .brand .dot{width:50px;height:50px}
.nav{right:178px;top:38px;display:flex;gap:25px;align-items:center;font-size:12px;font-weight:500;text-transform:uppercase;color:#222}
.hero h1{left:174px;top:170px;width:420px;font-size:32px;line-height:44px;font-weight:700;color:var(--brown);white-space:nowrap}
.btn{display:inline-flex;align-items:center;justify-content:center;background:#2b2b2b;color:#fff;font-size:12px;font-weight:600;border-radius:4px;box-shadow:0 3px 8px rgba(0,0,0,.25)}
.hero .btn{left:174px;top:365px;width:172px;height:33px}
.hero-art{left:640px;top:90px;width:460px;height:400px;border-radius:48% 52% 45% 55%;background:radial-gradient(ellipse at 50% 50%,#e8c86a 0%,#d8b261 30%,#c9b091 55%,rgba(220,200,172,0) 75%)}
/* sections */
.sec-title{width:1200px;left:0;text-align:center;font-size:22px;font-weight:600;color:#333}
.cat{width:150px;text-align:center;font-size:13px;line-height:19px;color:#333}
.cat .circle{width:106px;height:106px;border-radius:50%;margin:0 auto 14px}
.prod{width:180px;height:217px;background:var(--card);border-radius:6px;box-shadow:0 2px 6px rgba(0,0,0,.08);text-align:center}
.prod .thumb{width:72px;height:76px;margin:24px auto 0;border-radius:50%}
.prod .icons{position:absolute;right:16px;top:18px;display:flex;flex-direction:column;gap:8px}
.prod .name{font-size:12.5px;line-height:19px;color:#333;padding:12px 10px 0;height:72px}
.prod .price{font-size:15px;font-weight:700;color:var(--price);margin-top:12px}
.dots{left:574px;top:1185px;display:flex;gap:4px}
.dots span{width:7px;height:7px;border-radius:50%;background:#cfe3e3}
.dots span:first-child{background:#137a7a}
.collage{border-radius:8px}
.personal h2{font-size:22px;font-weight:600;color:#333}
.personal p{font-family:"Lato",sans-serif;font-size:10.5px;line-height:20px;color:#555;width:435px}
.personal u{text-decoration:underline}
.band{left:0;top:1635px;width:1200px;height:292px;background:linear-gradient(110deg,#18202b 0%,#2c3744 45%,#1b232d 100%);text-align:center;color:#fff}
.band h2{font-size:22px;font-weight:600;margin-top:90px}
.band p{font-size:13px;margin-top:14px}
.band .gold{display:inline-flex;margin-top:14px;width:171px;height:32px;background:var(--gold);color:#222;font-size:12px;font-weight:600;border-radius:4px;align-items:center;justify-content:center}
.style-img{width:256px;height:142px;border-radius:8px}
.style-box{width:220px;height:89px;background:#efe6d8;border-radius:8px;text-align:center;font-family:"Lato",sans-serif;font-size:10.5px;line-height:20px;color:#555;padding-top:5px}
.style-box b{font-family:"Archivo",sans-serif;font-size:13px;color:#333;display:block;line-height:18px}
.style-box .hl{color:#1a8a9a}
.review{width:266px;height:139px;background:#fff;border-radius:6px;box-shadow:0 2px 10px rgba(0,0,0,.12);padding:18px 19px;font-family:"Lato",sans-serif;font-size:10.5px;line-height:20px;color:#666}
.review.main{height:173px;padding-top:20px}
.review b{font-family:"Archivo",sans-serif;font-size:11px;color:#222;display:block;line-height:14px}
.review .stars{color:#e2b21c;font-size:8px;letter-spacing:1px;line-height:12px;margin-bottom:8px}
.footer{left:0;top:2687px;width:1200px;height:402px;background:var(--dark);color:#fff}
.footer .brand{left:174px;top:95px;color:#fff;font-size:18px;line-height:22px}
.footer .brand .dot{width:58px;height:58px}
.perks{left:174px;top:2630px;width:852px;height:87px;background:var(--bar);border-radius:8px;display:flex;align-items:center;justify-content:space-around;padding:0 20px;font-size:12px;font-weight:600;color:#222}
.perks div{display:flex;align-items:center;gap:10px}
.perks i{width:24px;height:24px;border-radius:50%;background:#cfc4a8;display:inline-flex;align-items:center;justify-content:center}
.fcol h4{font-size:14px;font-weight:500;text-decoration:underline;text-underline-offset:3px;margin-bottom:16px}
.fcol a{display:block;font-size:10.5px;line-height:24px;color:#eee;text-decoration:none}
.fline{left:0;width:1200px;height:1px;background:var(--dark-line)}
.contact{display:flex;align-items:center;gap:14px;font-size:13px;font-weight:600}
.pay{right:174px;top:3053px;display:flex;gap:10px}
.pay span{width:20px;height:13px;border-radius:2px;background:#8a8172}
</style>
</head>
<body>

<!-- Hero -->
<section class="abs hero">
  <div class="abs brand"><span class="dot"></span><span class="word"><span>Kestrel</span><span>Hoops</span></span></div>
  <nav class="abs nav">
    <span>Shop by Material</span><span>Shop by Color</span><span>Try at Home</span>
    <svg width="20" height="20" viewBox="0 0 20 20"><circle cx="8" cy="8" r="6.5" fill="none" stroke="#333" stroke-width="2"/><line x1="13" y1="13" x2="19" y2="19" stroke="#333" stroke-width="2"/></svg>
    <svg width="18" height="20" viewBox="0 0 18 20"><rect x="2" y="6" width="14" height="13" rx="2" fill="#333"/><path d="M5 7V5a4 4 0 0 1 8 0v2" fill="none" stroke="#333" stroke-width="2"/></svg>
  </nav>
  <h1 class="abs">Elevate Your Style:<br>Handcrafted Rings<br>with Free Fast Delivery<br>&amp; Hassle Free Returns</h1>
  <span class="abs btn">Discover Our Collections</span>
  <div class="abs hero-art" role="img" aria-label="Three gold and silver wedding bands resting in a cracked sand nest"></div>
</section>

<!-- Categories -->
<h2 class="abs sec-title" style="top:592px">Our Product Categories</h2>
<div class="abs cat" style="left:150px;top:644px"><div class="circle" role="img" aria-label="Black collection ring" style="background:radial-gradient(circle,#444,#050505 70%)"></div>Strong Fearless<br>Majestics</div>
<div class="abs cat" style="left:300px;top:644px"><div class="circle" role="img" aria-label="Silver collection ring" style="background:radial-gradient(circle,#f0f0f0,#b8b8b8 80%)"></div>Calm Sophisticated<br>Elegant</div>
<div class="abs cat" style="left:451px;top:644px"><div class="circle" role="img" aria-label="Blue collection ring" style="background:radial-gradient(circle,#2a5fb0,#1496c8 55%)"></div>Constant Loyal<br>True</div>
<div class="abs cat" style="left:601px;top:644px"><div class="circle" role="img" aria-label="Gold collection ring" style="background:radial-gradient(circle,#e2b84a,#efe2a8 75%)"></div>Bright Brilliant<br>Classic</div>
<div class="abs cat" style="left:751px;top:644px"><div class="circle" role="img" aria-label="Brown collection ring" style="background:radial-gradient(circle,#a0603c,#5a2a1a 75%)"></div>Authentic<br>Genuine Simple</div>
<div class="abs cat" style="left:900px;top:644px"><div class="circle" role="img" aria-label="Rose gold collection ring" style="background:radial-gradient(circle,#d9a07a,#f8d4b4 70%)"></div>Romantic<br>Vintage Sublime</div>

<!-- Top rated -->
<h2 class="abs sec-title" style="top:881px">Top Rated Products</h2>
<div class="abs prod" style="left:174px;top:934px">
  <div class="icons"><svg width="10" height="10" viewBox="0 0 10 10"><path d="M0 1h2l1 5h6l1-4H3" fill="none" stroke="#9a4a12" stroke-width="1.5"/><circle cx="4" cy="8.5" r="1" fill="#9a4a12"/><circle cx="8" cy="8.5" r="1" fill="#9a4a12"/></svg><svg width="11" height="10" viewBox="0 0 11 10"><path d="M5.5 9L1 4.5a2.2 2.2 0 0 1 4.5-2.5A2.2 2.2 0 0 1 10 4.5z" fill="none" stroke="#9a4a12"/></svg></div>
  <div class="thumb" role="img" aria-label="Blue and silver tungsten ring" style="background:radial-gradient(circle,transparent 40%,#2154c0 42%,#9aa8c8 70%,transparent 72%)"></div>
  <div class="name">Blue Harbour – Men's Tungsten Ring – Silver and Blue Guy's Band 8mm</div><div class="price">£49.99</div>
</div>
<div class="abs prod" style="left:398px;top:934px">
  <div class="icons"><svg width="10" height="10" viewBox="0 0 10 10"><path d="M0 1h2l1 5h6l1-4H3" fill="none" stroke="#9a4a12" stroke-width="1.5"/><circle cx="4" cy="8.5" r="1" fill="#9a4a12"/><circle cx="8" cy="8.5" r="1" fill="#9a4a12"/></svg><svg width="11" height="10" viewBox="0 0 11 10"><path d="M5.5 9L1 4.5a2.2 2.2 0 0 1 4.5-2.5A2.2 2.2 0 0 1 10 4.5z" fill="none" stroke="#9a4a12"/></svg></div>
  <div class="thumb" role="img" aria-label="Gold tungsten ring with silver band" style="background:radial-gradient(circle,transparent 40%,#e0b140 42%,#c9b88a 70%,transparent 72%)"></div>
  <div class="name">Cassian – Men's Tungsten Ring – Gold with Silver Band for Him 8mm</div><div class="price">£56.00</div>
</div>
<div class="abs prod" style="left:622px;top:934px">
  <div class="icons"><svg width="10" height="10" viewBox="0 0 10 10"><path d="M0 1h2l1 5h6l1-4H3" fill="none" stroke="#9a4a12" stroke-width="1.5"/><circle cx="4" cy="8.5" r="1" fill="#9a4a12"/><circle cx="8" cy="8.5" r="1" fill="#9a4a12"/></svg><svg width="11" height="10" viewBox="0 0 11 10"><path d="M5.5 9L1 4.5a2.2 2.2 0 0 1 4.5-2.5A2.2 2.2 0 0 1 10 4.5z" fill="none" stroke="#9a4a12"/></svg></div>
  <div class="thumb" role="img" aria-label="Silver titanium ring" style="background:radial-gradient(circle,transparent 40%,#b8b8b8 42%,#e8e8e8 70%,transparent 72%)"></div>
  <div class="name">Summit – Men's Titanium Ring – Silver Band for Him 6mm or 8mm</div><div class="price">£45.00</div>
</div>
<div class="abs prod" style="left:846px;top:934px">
  <div class="icons"><svg width="10" height="10" viewBox="0 0 10 10"><path d="M0 1h2l1 5h6l1-4H3" fill="none" stroke="#9a4a12" stroke-width="1.5"/><circle cx="4" cy="8.5" r="1" fill="#9a4a12"/><circle cx="8" cy="8.5" r="1" fill="#9a4a12"/></svg><svg width="11" height="10" viewBox="0 0 11 10"><path d="M5.5 9L1 4.5a2.2 2.2 0 0 1 4.5-2.5A2.2 2.2 0 0 1 10 4.5z" fill="none" stroke="#9a4a12"/></svg></div>
  <div class="thumb" role="img" aria-label="Black tungsten ring with green fibre inlay" style="background:radial-gradient(circle,transparent 40%,#111 42%,#1f4a32 70%,transparent 72%)"></div>
  <div class="name">Verdant – Men's Tungsten Ring – Black with Green Fibre Inlay Guy's Band 8mm</div><div class="price">£49.00</div>
</div>
<div class="abs dots"><span></span><span></span><span></span><span></span><span></span></div>

<!-- Personalise -->
<div class="abs collage" style="left:262px;top:1307px;width:204px;height:113px;background:linear-gradient(135deg,#1a80c8,#2a4e90 60%,#1b6db0)" role="img" aria-label="Blue collection rings with engraving"></div>
<div class="abs collage" style="left:174px;top:1429px;width:166px;height:104px;background:linear-gradient(135deg,#c9a060,#e9d29a 50%,#b8a880)" role="img" aria-label="Gold collection rings with engraving"></div>
<div class="abs collage" style="left:351px;top:1429px;width:207px;height:126px;background:linear-gradient(135deg,#4a1a14,#7a2a22 50%,#3a1410)" role="img" aria-label="Brown collection rings with engraving"></div>
<div class="abs personal" style="left:596px;top:1284px">
  <h2>Personalise and Engrave your Ring</h2>
  <p style="margin-top:14px">Yes we can do ring engraving….<br>
  Add heartfelt meaning and sentiment to your ring with a <u>personalised ring engraving</u>. The perfect way to add that little extra something to your ring, whether for yourself, or as a gift. Choose your very own ring engraving to give your ring personal meaning, symbolise your commitment and love, or mark a special date. Whatever you choose to engrave on your ring, your engraving will tell your own personal story and will enrich your ring as a cherished keepsake for years to come.<br>
  Add a name, date, initials, or short message and we will engrave it to the inside of your ring. You will not only have an extraordinary ring but one that is symbolic, meaningful, and full of sentiment..........</p>
</div>
<span class="abs btn" style="left:596px;top:1539px;width:153px;height:33px">Personalize Your Ring</span>

<!-- Wedding bands banner -->
<section class="abs band" role="img" aria-label="Close-up of a man's hand wearing a dark wedding band">
  <h2>Men's Wedding Bands</h2>
  <p>FALL WEDDING SALE- 20% OFF SITEWIDE</p>
  <span class="gold">Discover Our Collections</span>
</section>

<!-- Styles -->
<h2 class="abs sec-title" style="top:1984px">Seeking Uniqueness? Explore Our Range of Distinct Ring Styles</h2>
<div class="abs style-img" style="left:174px;top:2037px;background:linear-gradient(135deg,#2e7a2e,#5aa84a 50%,#3a8a36)" role="img" aria-label="Wood inlay rings on fern leaves"></div>
<div class="abs style-box" style="left:192px;top:2146px"><b>Wood</b>For the man who loves the outdoors.<br><span class="hl">Wood rings</span> in tungsten and titanium<br>Adventurous | Free Spirited | Down-to-Earth</div>
<div class="abs style-img" style="left:471px;top:2037px;background:linear-gradient(180deg,#1a1410,#3a2a1a 45%,#2a5a80)" role="img" aria-label="Meteorite rings above the earth"></div>
<div class="abs style-box" style="left:489px;top:2146px"><b>Meteorite</b><span class="hl">Meteorite rings</span> that are out of this world<br>For a completely different style.<br>Unique | Distinctive | Magnificent</div>
<div class="abs style-img" style="left:770px;top:2037px;background:linear-gradient(135deg,#6a8a5a,#c8b070 40%,#3a6a8a 75%,#8aa0a0)" role="img" aria-label="Abalone shell inlay rings"></div>
<div class="abs style-box" style="left:788px;top:2146px"><b>Abalone Shell</b>For the ocean loving man<br><span class="hl">Shell rings</span> in tungsten and titanium<br>Iridescent | Vibrant | Stunning</div>

<!-- Reviews -->
<h2 class="abs sec-title" style="top:2325px">We Love Happy Customers</h2>
<div class="abs review" style="left:-102px;top:2393px"><b>&nbsp;</b><div class="stars">&nbsp;</div>Great from start to finish, loved the try the rings before I buy. Replies were excellent, quick replies and helpful......</div>
<div class="abs review" style="left:183px;top:2393px"><b>Maya Thornton</b><div class="stars">★★★★★</div>My partner wanted a black ring and he is absolutely in love with it. We also purchased the option to have it engraved and the support and communication throughout .......</div>
<div class="abs review main" style="left:468px;top:2376px"><b>Owen Pritchard</b><div class="stars">★★★★★</div>I absolutely love my ring, it's so shiny and love the colour of the blue with carbon and will be definitely be buying again from this company again. Speedy delivery and very good customer service.</div>
<div class="abs review" style="left:752px;top:2393px"><b>Daniel Ashby</b><div class="stars">★★★★★</div>Fantastic service from start to finish, loved the fact I could try the rings before I buy. Communications were excellent, quick replies and always helpful......</div>
<div class="abs review" style="left:1035px;top:2393px"><b>Hannah Corrie</b><div class="stars">★★★★★</div>This is my 2nd purchase from here. The hubby adores these rings and rings to match his watch collection are extremely high .......</div>

<!-- Footer -->
<footer class="abs footer">
  <div class="abs brand"><span class="dot"></span><span class="word"><span>Kestrel</span><span>Hoops</span></span></div>
  <div class="abs fcol" style="left:436px;top:92px"><h4>Quick Links</h4><a>FREE ring sizer</a><a>FREE Delivery |</a><a>Returns and Exchanges</a><a>Try at Home</a><a>Ring Engraving</a></div>
  <div class="abs fcol" style="left:603px;top:92px"><h4>Ring Guide</h4><a>&nbsp;The Best Tungsten and Titanium Rings - Full Guide</a><a>&nbsp;How is Tungsten or Titanium Ring Size Measured?</a><a>&nbsp;Black, Silver Gold - The best colors for mens tungsten</a><a>&nbsp;and titanium rings</a><a>&nbsp;Whats better tungsten or titanium for a mens ring</a></div>
  <div class="abs fcol" style="left:932px;top:92px"><h4>Important Links</h4><a>Contact Us</a><a>Terms of Service</a><a>Privacy Policy</a><a>Blog</a></div>
  <div class="abs fline" style="top:256px"></div>
  <div class="abs contact" style="left:174px;top:288px"><svg width="20" height="26" viewBox="0 0 20 26"><path d="M10 0a10 10 0 0 0-10 10c0 7 10 16 10 16s10-9 10-16A10 10 0 0 0 10 0z" fill="#fff"/><circle cx="10" cy="10" r="4" fill="#2a2117"/></svg>14 Alder Row, Brackwell, BW4 7QT</div>
  <div class="abs contact" style="left:566px;top:288px"><svg width="24" height="24" viewBox="0 0 24 24"><path d="M5 1l4 0 2 6-3 2c1 3 4 6 7 7l2-3 6 2v4c0 2-2 4-4 4C9 23 1 15 1 5c0-2 2-4 4-4z" fill="#fff"/></svg>01632 960418</div>
  <div class="abs contact" style="left:815px;top:290px"><svg width="26" height="18" viewBox="0 0 26 18"><rect x="1" y="1" width="24" height="16" fill="none" stroke="#fff" stroke-width="2"/><path d="M1 1l12 9 12-9" fill="none" stroke="#fff" stroke-width="2"/></svg>hello@kestrelhoops.com</div>
  <div class="abs fline" style="top:346px"></div>
  <div class="abs" style="left:174px;top:367px;font-size:11px;color:#eee">Copyright © 2024 Kestrel Hoops All Rights Reserved</div>
</footer>
<div class="abs pay" aria-label="Accepted payment methods"><span></span><span></span><span></span><span></span><span></span><span></span><span></span></div>

<div class="abs perks">
  <div><i><svg width="12" height="10" viewBox="0 0 12 10"><rect x="0" y="2" width="8" height="6" fill="#333"/><path d="M8 4h3l1 2v2H8z" fill="#333"/></svg></i>Free Delivery</div>
  <div><i><svg width="12" height="12" viewBox="0 0 12 12"><path d="M2 6a4 4 0 1 0 1.5-3.1" fill="none" stroke="#333" stroke-width="1.6"/><path d="M1 1v3h3" fill="none" stroke="#333" stroke-width="1.6"/></svg></i>Free Returns</div>
  <div><i><svg width="12" height="12" viewBox="0 0 12 12"><circle cx="6" cy="6" r="4.5" fill="none" stroke="#333" stroke-width="1.6"/></svg></i>Every Ring Stock</div>
  <div><i><svg width="12" height="12" viewBox="0 0 12 12"><path d="M2 6l3 3 5-6" fill="none" stroke="#333" stroke-width="1.8"/></svg></i>Fast Delivery</div>
  <div><i><svg width="12" height="12" viewBox="0 0 12 12"><circle cx="6" cy="6" r="2" fill="#333"/><circle cx="6" cy="1.5" r="1" fill="#333"/><circle cx="6" cy="10.5" r="1" fill="#333"/><circle cx="1.5" cy="6" r="1" fill="#333"/><circle cx="10.5" cy="6" r="1" fill="#333"/></svg></i>Customer Images</div>
</div>

</body>
</html>
```